Highlight Document Over Image for Slide

We are seeking a graphic designer to overlay a news article on an image that pertains to the article, aiming for a stylish yet professional appearance. Given the limited resources, we encourage you to use your imagination and go beyond what basic tools like PowerPoint can offer.

```html
<!DOCTYPE html>
<html lang="en">
<head>
<meta charset="utf-8">
<title>Introduction or Possession of Contraband Items</title>
<link rel="stylesheet" href="https://fonts.googleapis.com/css2?family=Tinos:wght@400;700&display=swap">
<style>
  :root {
    --page-bg: #efefef;
    --hills: #a38b5d;
    --hills-dry: #b39a68;
    --town: #6f6c5c;
    --complex: #7c7168;
    --roofs: #8f8780;
    --brick: #8a5a4e;
    --shore: #8c7a5a;
    --water: #5e5c51;
    --water-deep: #52514a;
    --panel: rgba(244, 244, 245, 0.95);
    --ink: #1e1410;
    --pill: #5a5a56;
    --pill-ring: #ffffff;
    --rule: rgba(255, 255, 255, 0.8);
  }
  * { margin: 0; padding: 0; box-sizing: border-box; }
  html, body {
    width: 1200px;
    height: 1200px;
    overflow: hidden;
    background: var(--page-bg);
  }
  .slide {
    position: absolute;
    left: 23px;
    top: 238px;
    width: 1157px;
    height: 656px;
    overflow: hidden;
  }
  .aerial-map {
    position: absolute;
    inset: 0;
    background:
      radial-gradient(ellipse 190px 120px at 360px 270px, rgba(150, 135, 125, 0.85), transparent 75%),
      radial-gradient(ellipse 150px 170px at 520px 430px, rgba(128, 100, 92, 0.85), transparent 75%),
      radial-gradient(ellipse 120px 90px at 430px 160px, rgba(200, 200, 195, 0.55), transparent 75%),
      radial-gradient(ellipse 140px 90px at 250px 150px, rgba(110, 105, 100, 0.8), transparent 75%),
      radial-gradient(ellipse 110px 140px at 120px 200px, rgba(125, 120, 110, 0.8), transparent 75%),
      radial-gradient(ellipse 170px 70px at 160px 400px, rgba(150, 120, 80, 0.8), transparent 75%),
      radial-gradient(ellipse 230px 150px at 900px 110px, rgba(95, 95, 80, 0.85), transparent 75%),
      radial-gradient(ellipse 320px 60px at 420px 20px, rgba(180, 155, 105, 0.9), transparent 80%),
      radial-gradient(ellipse 420px 220px at 460px 330px, rgba(124, 113, 104, 0.9), transparent 80%),
      radial-gradient(ellipse 520px 200px at 620px 560px, rgba(82, 81, 74, 0.9), transparent 80%),
      radial-gradient(ellipse 380px 260px at 120px 560px, rgba(86, 85, 76, 0.95), transparent 80%),
      linear-gradient(180deg, var(--hills) 0%, var(--hills-dry) 12%, var(--complex) 38%, var(--complex) 52%, var(--water) 72%, var(--water-deep) 100%);
  }
  .header-rule {
    position: absolute;
    left: 0;
    right: 0;
    top: 61px;
    height: 1px;
    background: var(--rule);
  }
  .article-panel {
    position: absolute;
    left: 592px;
    top: 153px;
    width: 565px;
    height: 365px;
    background: var(--panel);
    border-radius: 125px 0 0 100px / 185px 0 0 180px;
    font-family: "Tinos", "Times New Roman", serif;
    color: var(--ink);
  }
  .article-title {
    position: absolute;
    left: 113px;
    right: 10px;
    top: 33px;
    font-size: 21.2px;
    font-weight: 700;
    line-height: 28.6px;
    text-transform: uppercase;
  }
  .article-body {
    position: absolute;
    left: 113px;
    width: 437px;
    top: 105px;
    font-size: 17px;
    line-height: 23.05px;
  }
  .body-line {
    display: block;
    white-space: nowrap;
    text-align: justify;
    text-align-last: justify;
  }
  .body-line.last { text-align-last: left; }
  .page-number {
    position: absolute;
    left: 322px;
    top: 317px;
    width: 58px;
    height: 37px;
    border-radius: 19px;
    background: var(--pill);
    border: 3px solid var(--pill-ring);
    color: #ffffff;
    font-size: 14px;
    font-weight: 700;
    letter-spacing: 4px;
    text-align: center;
    line-height: 31px;
    padding-left: 4px;
  }
</style>
</head>
<body>
  <section class="slide">
    <div class="aerial-map" role="img" aria-label="Aerial satellite map of a waterfront prison complex with buildings, roads, dry hills and the bay below"></div>
    <div class="header-rule"></div>
    <article class="article-panel">
      <h1 class="article-title">20. Introduction or Possession of<br>Contraband Items</h1>
      <p class="article-body">
        <span class="body-line">Employees shall not introduce or possess unauthorized items</span>
        <span class="body-line">such as escape paraphernalia, weapons, facsimiles of</span>
        <span class="body-line">weapons, ammunition, wireless communication devices, cell</span>
        <span class="body-line">phones, tobacco or facsimiles of tobaccos products (e.g.</span>
        <span class="body-line">electronic vapor cigarettes) lighters or any other item not</span>
        <span class="body-line">specifically authorized by PD 04.04.100 “Custody, Security</span>
        <span class="body-line">and Safety Systems (Exempt)”, OP 04.04.100 “Gate Security”</span>
        <span class="body-line">or facility operating procedure in any facility where offenders</span>
        <span class="body-line last">are housed. Employees are responsible for any item in their</span>
      </p>
      <div class="page-number">36</div>
    </article>
  </section>
</body>
</html>
```